Youth deer hunt give away flyer.

We need a flyer designed for a youth deer hunt giveaway that we are doing. We are an Illinois whitetail deer hunting outfitter. We house and feed our clients as well as providing them with a guided deer hunt. It needs to include images as well as details about the giveaway. Im looking for a proffesional, looking flyer
Updates

Target Market(s)

rednecks, hunters

Industry/Entity Type

Hunting

Font styles to use
Serif
Sans Serif

Colors
000000
dbdbdb
ffffff
474747

Requirements
Must have
• not sure
Nice to have
• not sure
Should not have
• not sure

```html
<!DOCTYPE html>
<html lang="en">
<head>
<meta charset="utf-8">
<title>2018 Youth Firearm Hunt Flyer</title>
<link rel="stylesheet" href="https://fonts.googleapis.com/css2?family=Alfa+Slab+One&family=Montserrat:wght@400;600;800&family=Playfair+Display:wght@400;700&display=swap">
<style>
  :root {
    --black: #000000;
    --light-grey: #dbdbdb;
    --white: #ffffff;
    --dark-grey: #474747;
    --band: #3a3a3a;
    --forest-dark: #3b2c1c;
    --forest-mid: #6b5030;
    --forest-light: #8a6a3e;
    --field-green: #6f9a3c;
    --page: #e9e9e9;
  }
  * { box-sizing: border-box; margin: 0; padding: 0; }
  html, body { width: 1200px; height: 900px; overflow: hidden; }
  body {
    background: var(--page);
    font-family: "Montserrat", Arial, sans-serif;
    display: flex; align-items: center; justify-content: center;
  }
  .flyer {
    position: relative;
    width: 620px; height: 860px;
    background: var(--white);
    box-shadow: 0 8px 24px rgba(0,0,0,.25);
    overflow: hidden;
  }
  .hero {
    position: absolute; left: 0; top: 0; width: 620px; height: 460px;
    background: linear-gradient(160deg, var(--forest-dark) 0%, var(--forest-mid) 45%, var(--forest-light) 70%, #4f5a2a 100%);
  }
  .headline {
    position: absolute; left: 34px; top: 30px;
    font-family: "Alfa Slab One", Georgia, serif;
    color: var(--white); line-height: 1.02;
    text-shadow: 0 2px 4px rgba(0,0,0,.45);
  }
  .headline .line-1 { font-size: 58px; letter-spacing: 2px; }
  .headline .line-2 { font-size: 40px; letter-spacing: 2px; }
  .headline .dates { font-size: 24px; letter-spacing: 1px; margin-top: 4px; }
  .inset {
    position: absolute; right: 0; top: 185px; width: 290px; height: 150px;
    border: 4px solid var(--light-grey); border-right: 0;
    background: linear-gradient(180deg, #5d6b4a 0%, #7f8a6a 45%, var(--field-green) 70%, #5f8a30 100%);
  }
  .inset svg { position: absolute; left: 118px; top: 40px; }
  .follow {
    position: absolute; right: 0; top: 335px; width: 250px; height: 46px;
    background: var(--band);
    clip-path: polygon(18px 0, 100% 0, 100% 100%, 0 100%);
    display: flex; align-items: center; justify-content: flex-end; gap: 8px;
    padding-right: 20px;
    font-family: "Playfair Display", Georgia, serif;
    color: var(--white); font-size: 13px; letter-spacing: 1px;
  }
  .follow .social { width: 12px; height: 12px; background: var(--light-grey); border-radius: 2px; }
  .call {
    position: absolute; left: 34px; top: 388px;
    font-family: "Alfa Slab One", Georgia, serif;
    color: var(--white); font-size: 28px; letter-spacing: 1px;
    text-shadow: 0 2px 4px rgba(0,0,0,.5);
  }
  .details {
    position: absolute; left: 0; top: 440px; width: 620px; height: 150px;
    background: var(--band);
    clip-path: polygon(0 0, 100% 0, 100% 62%, 0 100%);
    padding: 14px 20px 0 28px;
  }
  .details ul { list-style: none; }
  .details li {
    color: var(--white); font-size: 12px; line-height: 22px; white-space: nowrap;
    display: flex; align-items: center; gap: 10px;
  }
  .details li::before {
    content: ""; width: 9px; height: 9px; flex: none;
    background:
      linear-gradient(var(--white),var(--white)) 0 0/4px 4px no-repeat,
      linear-gradient(var(--white),var(--white)) 5px 0/4px 4px no-repeat,
      linear-gradient(var(--white),var(--white)) 0 5px/4px 4px no-repeat,
      linear-gradient(var(--white),var(--white)) 5px 5px/4px 4px no-repeat;
  }
  .section-title {
    font-family: "Alfa Slab One", Georgia, serif;
    font-size: 15px; color: var(--dark-grey); letter-spacing: 1px;
    display: flex; align-items: center; gap: 8px; margin-bottom: 10px;
  }
  .section-title::before { content: ""; width: 14px; height: 12px; background: var(--dark-grey); }
  .about {
    position: absolute; left: 34px; top: 612px; width: 335px;
    font-size: 11px; line-height: 17px; color: var(--dark-grey);
  }
  .about p + p { margin-top: 10px; }
  .contact {
    position: absolute; left: 392px; top: 612px; width: 210px;
    font-size: 11px; line-height: 18px; color: var(--dark-grey);
  }
  .contact .name { font-family: "Playfair Display", Georgia, serif; font-weight: 700; letter-spacing: .5px; }
  .brand {
    position: absolute; left: 392px; top: 770px; width: 200px;
    display: flex; align-items: center; gap: 10px;
    font-family: "Playfair Display", Georgia, serif;
    font-size: 17px; color: var(--black); line-height: 1.1;
  }
  .brand .mark { width: 22px; height: 22px; border-radius: 50%; background: var(--black); flex: none; }
</style>
</head>
<body>
  <article class="flyer">
    <div class="hero" role="img" aria-label="Photo of a hunter kneeling with a harvested whitetail buck in an autumn forest"></div>

    <header class="headline">
      <div class="line-1">2018 YOUTH</div>
      <div class="line-2">FIREARM HUNT</div>
      <div class="dates">OCTOBER 6-8, 2018</div>
    </header>

    <div class="inset" role="img" aria-label="Photo of a whitetail buck standing on a green field at the tree line">
      <svg width="40" height="40" viewBox="0 0 40 40" aria-hidden="true">
        <circle cx="20" cy="20" r="13" fill="none" stroke="#111" stroke-width="2.5"/>
        <circle cx="20" cy="20" r="3" fill="#111"/>
        <line x1="20" y1="2" x2="20" y2="12" stroke="#111" stroke-width="2.5"/>
        <line x1="20" y1="28" x2="20" y2="38" stroke="#111" stroke-width="2.5"/>
        <line x1="2" y1="20" x2="12" y2="20" stroke="#111" stroke-width="2.5"/>
        <line x1="28" y1="20" x2="38" y2="20" stroke="#111" stroke-width="2.5"/>
      </svg>
    </div>

    <div class="follow">FOLLOW US ON <span class="social"></span><span class="social"></span></div>

    <div class="call">CALL (217)555-0148</div>

    <section class="details">
      <ul>
        <li>4 night stay in our private cabin that include meals for 2 parents and the child.</li>
        <li>Guided shotgun hunt on strictly managed properties.</li>
        <li>Ground blinds in place.</li>
        <li>Permit and license fees are the hunters responsibility.</li>
      </ul>
    </section>

    <section class="about">
      <h2 class="section-title">ABOUT US</h2>
      <p>Harlan Ridge Outfitting is a family owned and operated deer hunting outfitter located in Morgan and Scott Counties in west central Illinois. We provide low pressure, trophy whitetail hunts on privately owned farms across the region. The Harlans are lifelong residents and hunters of Morgan County, with the family farm being established well over 150 years ago.</p>
      <p>To go along with guiding deer and turkey hunters, we also offer a wide variety of professional hunting services that include whitetail land consulting, scouting services, CRP and food plot plantings and more.</p>
    </section>

    <section class="contact">
      <h2 class="section-title">CONTACT</h2>
      <p>hello@harlanridgehunts.com</p>
      <p>www.harlanridgehunts.com</p>
      <p class="name">WADE HARLAN:</p>
      <p>1480 Ridge Road Jacksonville,<br>Illinois 62650</p>
    </section>

    <div class="brand"><span class="mark"></span><span>HARLAN RIDGE OUTFITTING</span></div>
  </article>
</body>
</html>
```